Simple Business Card Design for Tavlo

Job:

Make a very simple, minimalist business card design with my details including adjusted logo. One side to be white (with logo & text). Other side to be yellow - try plain or with logo (or part of logo eg Z). Need business card to have continuity with website.

Logo:
Our logo is made from a free download font website:
http://www.typewell.net/search.php?q=rubber
but the spacing/kerning needs correcting/adjusting as the font spaces unevenly between letters (see attached files). Need logo to be very crisp/sharp when printed.

Printing:
We will be using Plika.com so the design needs to conform to their requirements, see here:

http://uk.plika.com/products/luxe/business-cards.html (scroll down for dimensions and guidelines)

Design:

must say "plant-based food consulting" underneath logo or somewhere
no address needed in contact section
sharp corners (not rounded)
one side white, one side yellow

name: Rosalind Whitcombe
1xmobile number: +44 7700900463
1xtwiiter: @brimcounsel
website address www.orchardtable.com
email address brim@orchardtable.com

Should be easy quick job, prompt + detailed feedback given, am online in UK 9am-10pm for next 3 days. Website is www.orchardtable.com

Industry/Entity Type

Business

Requirements
Must have
• The logo must be corrected. The kerning is not right.

Please use a warm-grey for text

Please submit in matt format, we will be printing matt finish.

Should not have
• Avoid using banners or curvy highlights

Please avoid using black

Please avoid submitting in gloss finish

```html
<!DOCTYPE html>
<html lang="en">
<head>
<meta charset="utf-8">
<title>Brim business card</title>
<link rel="stylesheet" href="https://fonts.googleapis.com/css2?family=Cinzel:wght@500;700&family=Cormorant+SC:wght@500;600&display=swap">
<style>
  :root {
    --backdrop: #e4e4e3;
    --card-white: #ffffff;
    --card-yellow: #f0e04a;
    --warm-grey: #7a726a;
    --warm-grey-dark: #5e5750;
    --accent: #b9a416;
  }
  * { box-sizing: border-box; margin: 0; padding: 0; }
  html, body {
    width: 1200px;
    height: 720px;
    overflow: hidden;
    background: var(--backdrop);
  }
  .canvas {
    position: relative;
    width: 1200px;
    height: 720px;
  }
  .card {
    position: absolute;
    top: 242px;
    width: 420px;
    height: 240px;
  }
  .card--front {
    left: 147px;
    background: var(--card-white);
  }
  .card--back {
    left: 633px;
    background: var(--card-yellow);
    display: flex;
    align-items: center;
    justify-content: center;
  }

  .wordmark {
    font-family: "Cinzel", serif;
    font-weight: 700;
    color: var(--warm-grey-dark);
    letter-spacing: 0.06em;
    line-height: 1;
    text-align: center;
  }
  .card--front .wordmark {
    position: absolute;
    top: 38px;
    left: 0;
    right: 0;
    font-size: 50px;
  }
  .card--back .wordmark { font-size: 66px; }

  .tagline {
    position: absolute;
    top: 96px;
    left: 0;
    right: 0;
    text-align: center;
    font-family: "Cormorant SC", serif;
    font-weight: 600;
    font-size: 11px;
    letter-spacing: 0.14em;
    color: var(--warm-grey);
    line-height: 1;
  }

  .person {
    position: absolute;
    top: 132px;
    left: 0;
    right: 0;
    text-align: center;
  }
  .person__name {
    font-family: "Cinzel", serif;
    font-weight: 700;
    font-size: 12px;
    color: var(--warm-grey-dark);
    line-height: 1.1;
  }
  .person__role {
    font-family: "Cormorant SC", serif;
    font-weight: 500;
    font-size: 11px;
    color: var(--warm-grey);
    line-height: 1.1;
  }

  .contacts {
    position: absolute;
    top: 172px;
    left: 0;
    right: 0;
    list-style: none;
    text-align: center;
    font-family: "Cormorant SC", serif;
    font-weight: 600;
    font-size: 10.5px;
    line-height: 13px;
    color: var(--warm-grey);
  }
  .contacts__label {
    font-family: "Cinzel", serif;
    font-weight: 700;
    font-size: 9px;
    color: var(--accent);
  }
</style>
</head>
<body>
  <main class="canvas">
    <section class="card card--front" aria-label="Card front">
      <div class="wordmark">BRIM</div>
      <p class="tagline">plant-based food consulting</p>
      <div class="person">
        <p class="person__name">Aldous Penrow</p>
        <p class="person__role">Manager</p>
      </div>
      <ul class="contacts">
        <li><span class="contacts__label">Phone :</span> +44 7700 900463</li>
        <li><span class="contacts__label">Mail :</span> brim@orchardtable.com</li>
        <li><span class="contacts__label">Web :</span> www.orchardtable.com</li>
        <li><span class="contacts__label">Twitter :</span> @brimcounsel</li>
      </ul>
    </section>
    <section class="card card--back" aria-label="Card back">
      <div class="wordmark">BRIM</div>
    </section>
  </main>
</body>
</html>
```